WP website design (Harrowgate)

We need a wordpress design for an established auction and real estate company based in Florida. The winning design will incorporate a professional color scheme with company logo in a clean layout. The design needs to consider that this will be developed on a responsive theme. Colors are those that will highlight the logo.

Industry/Entity Type

Real Estate

Font styles to use
Serif
Sans Serif

Colors

Designer to choose colors to be used in the design.

Requirements
Must have
• Navigation:
1) Home
2) Auctions
3) Online Auctions
4) About Us
5) Services
6) Real Estate Listings
7) References
8) Contact Us

Colors will be blue (#000066) / red (#B10000) and black or other complementary color. Tagline to be used "Since 1977, Proven Results." Slideshow to be placed in the header or body of home page - please use stock real estate image.

Widgets: 1) Email Sign-up 2) Social media icons for FB and LinkedIn 3) Featured Listings 4) Testimonials 5) Register button

Footer will have smaller company logo, attached logos and contact info:
Phone: (555) 261-0948 Mobile: (555) 718-3062
Email: mirelharrowgate@quellmail.example
Address: 58 E. Tamsin Avenue, Ste 410, Corvale Bay, ST 32599
Nice to have
• Use of a drop down menu:
Auctions-
1) Upcoming Auctions
2) Past Auctions

```html
<!DOCTYPE html>
<html lang="en">
<head>
<meta charset="utf-8">
<title>Harrowgate Auctions</title>
<link href="https://fonts.googleapis.com/css2?family=Lato:wght@400;700&family=Roboto:wght@400;500;700&display=swap" rel="stylesheet">
<style>
:root{
  --red:#d71f26;
  --red-dark:#b10000;
  --red-light:#f0323e;
  --blue:#000066;
  --blue-mid:#103f80;
  --blue-btn:#2f3c9c;
  --text:#333;
  --muted:#555;
  --white:#fff;
}
*{margin:0;padding:0;box-sizing:border-box}
html,body{width:776px;height:1200px;overflow:hidden}
body{position:relative;background:var(--white);font-family:Roboto,Arial,sans-serif;color:var(--text)}
.abs{position:absolute}

/* header */
.brand{left:111px;top:26px;display:flex;align-items:center;gap:8px}
.brand-mark{width:28px;height:28px;background:var(--red-dark)}
.brand-name{font-family:Lato,sans-serif;font-weight:700;font-size:18px;color:var(--blue)}
.header-mail{right:172px;top:37px;font-size:8.3px;color:#222;display:flex;align-items:center;gap:5px;white-space:nowrap}
.btn-register{left:611px;top:33px;width:53px;height:17px;background:var(--blue-btn);color:#fff;font-size:7px;display:flex;align-items:center;justify-content:center;letter-spacing:.3px;border-radius:2px}

/* nav */
.main-nav{left:0;top:79px;width:776px;height:38px;background:var(--red)}
.main-nav ul{list-style:none;position:absolute;left:111px;top:0;display:flex;height:38px}
.main-nav li{font-size:9.3px;color:#fff;padding:0 10px;line-height:38px}
.main-nav li.active{background:var(--red-light)}
.dropdown{left:159px;top:117px;width:107px;height:46px;background:var(--red-light);padding:5px 0 0 9px}
.dropdown p{font-size:8.5px;color:#fff;line-height:19px}
.dropdown p::before{content:"";display:inline-block;border-left:4px solid #fff;border-top:3px solid transparent;border-bottom:3px solid transparent;margin-right:6px}

/* hero */
.hero{left:0;top:117px;width:776px;height:326px;background:linear-gradient(180deg,#8ea6c4 0%,#b9c3cc 35%,#7f7466 65%,#5b4a3a 100%)}
.hero-caption{left:111px;top:239px;width:368px;height:104px;background:rgba(25,25,25,.78);padding:14px 16px}
.hero-caption h1{font-family:Lato,sans-serif;font-weight:400;font-size:23px;color:#fff;line-height:28px}
.hero-caption p{font-family:Lato,sans-serif;font-size:9px;color:#eee;line-height:14.5px;margin-top:4px}
.dots{display:flex;gap:5px;margin-top:5px}
.dots span{width:12px;height:12px;border-radius:50%;background:#fff}
.dots span.on{background:var(--red-dark)}

/* welcome */
.section-title{font-family:Roboto,sans-serif;font-weight:400;color:var(--red-dark);font-size:16px;letter-spacing:.2px}
.welcome-title{left:0;width:766px;top:468px;text-align:center}
.welcome-text{left:115px;top:497px;width:551px;font-family:Arial,Helvetica,sans-serif;font-size:8.4px;line-height:15.5px;color:var(--text)}
.welcome-text span{display:block;white-space:nowrap;text-align:justify;text-align-last:justify}
.btn-more{left:363px;top:556px;width:37px;height:14px;background:var(--red-dark);color:#fff;font-size:6.5px;display:flex;align-items:center;justify-content:center}

/* featured */
.featured-title{left:113px;top:589px}
.arrow-btn{top:590px;width:17px;height:17px;border:1px solid var(--red-dark)}
.listing-grid{left:112px;top:624px;width:553px;height:170px;display:grid;grid-template-columns:repeat(4,1fr);grid-template-rows:repeat(2,1fr)}
.listing{position:relative}
.listing-hover{position:absolute;inset:0;background:rgba(232,120,128,.85);padding:28px 11px 0;color:#fff}
.listing-hover h3{font-weight:400;font-size:9.5px}
.listing-hover p{font-size:7px;white-space:nowrap}
.listing-hover .tools{display:flex;gap:4px;margin-top:6px}
.listing-hover .tools span{width:11px;height:9px;border:1px solid #f5d26a}

/* testimonials */
.testi-title{left:0;width:752px;top:819px;text-align:center}
.testimonial{top:862px;width:160px;text-align:center}
.avatar{width:40px;height:40px;border-radius:50%;margin:0 auto;background:radial-gradient(circle,#a98670,#4a3428)}
.testimonial time{display:block;font-family:Lato,sans-serif;font-size:6.5px;color:var(--red-dark);margin-top:13px}
.testimonial p{font-family:Lato,sans-serif;font-size:10.5px;line-height:12.3px;color:#555;margin-top:6px}

/* footer */
.site-footer{left:0;top:990px;width:776px;height:163px;background:var(--blue-mid)}
.footer-heading{font-size:7.8px;color:#fff;top:1014px;font-weight:400}
.contact-info{left:123px;top:1034px;width:135px;font-size:6.3px;line-height:9.8px;color:#fff}
.contact-info p+p{margin-top:3px}
.social{top:1103px;width:19px;height:19px;border-radius:50%;background:#2e4f86;border:2px solid #5b77a3}
.news-thumb{left:311px;width:37px;height:31px;background:linear-gradient(135deg,#dfe3e8,#6b7178);border:1px solid #fff}
.news-text{left:354px;color:#fff;font-size:7px;line-height:13px}
.news-text small{font-size:6px}
.newsletter-input{left:524px;top:1032px;width:104px;height:19px;background:#fff;border:1px solid #ccc;font-size:6.3px;font-style:italic;color:#666;padding:5px 6px}
.btn-subscribe{left:525px;top:1063px;width:62px;height:21px;background:#222;color:#fff;font-size:7.5px;display:flex;align-items:center;justify-content:center}
.badge{top:1109px;height:27px;background:#fff}

.footer-bar{left:0;top:1153px;width:776px;height:47px;background:var(--red-dark)}
.footer-bar nav{position:absolute;top:7px;left:0;width:776px;font-size:6.3px;color:#fff}
.footer-bar nav span{position:absolute}
.copyright{position:absolute;top:30px;width:776px;text-align:center;font-size:6px;color:#fff}
.to-top{left:720px;top:1167px;width:17px;height:17px;background:#333;border:1px solid #aaa}
</style>
</head>
<body>

<header>
  <div class="abs brand"><span class="brand-mark"></span><span class="brand-name">Harrowgate Auctions</span></div>
  <div class="abs header-mail">
    <svg width="10" height="7" viewBox="0 0 10 7"><rect x=".5" y=".5" width="9" height="6" fill="#2b3b8f"/><path d="M.5 .5 5 4 9.5 .5" stroke="#fff" fill="none" stroke-width=".8"/></svg>
    info@harrowgate.example
  </div>
  <div class="abs btn-register">REGISTER</div>
</header>

<nav class="abs main-nav">
  <ul>
    <li>Home</li><li class="active">Auctions</li><li>Online Auctions</li><li>About Us</li><li>Services</li><li>Real Estate Listings</li><li>References</li><li>Contact Us</li>
  </ul>
</nav>

<section class="abs hero" role="img" aria-label="Large two-storey suburban house at dusk with lit windows and double garage"></section>
<div class="abs dropdown"><p>Upcoming Auctions</p><p>Past Auctions</p></div>
<div class="abs hero-caption">
  <h1>Since 1977, Proven Results</h1>
  <p>Lorem ipsum dolor sit amet, consectetur adipisc ing elit. Aliquam viverra consecte-<br>tur nibh a blan dit. Proin at amet consectetur adipisc lacinia nunc.</p>
  <div class="dots"><span class="on"></span><span></span><span></span><span></span></div>
</div>

<h2 class="abs section-title welcome-title">WELCOME TO HARROWGATE</h2>
<p class="abs welcome-text">
  <span>Lorem Ipsum is simply dummy text of the printing and typesetting industry. Lorem Ipsum has been the industry's standard dummy text ever since</span>
  <span>the 1500s, when an unknown printer took a galley of type and scrambled it to make a type specimen book. It has survived not only five centuries</span>
  <span>Lorem Ipsum is simply dummy text of the printing and typesetting industry. Lorem Ipsum has been the industry's standard dummy text ever since</span>
</p>
<div class="abs btn-more">MORE</div>

<h2 class="abs section-title featured-title">FEATURED LISTINGS</h2>
<svg class="abs arrow-btn" style="left:626px" viewBox="0 0 17 17"><path d="M9.5 5 6 8.5 9.5 12" stroke="#b10000" fill="none" stroke-width="1.3"/></svg>
<svg class="abs arrow-btn" style="left:647px" viewBox="0 0 17 17"><path d="M7.5 5 11 8.5 7.5 12" stroke="#b10000" fill="none" stroke-width="1.3"/></svg>

<div class="abs listing-grid">
  <div class="listing" role="img" aria-label="Yellow family house with garden" style="background:linear-gradient(180deg,#6f9fd6,#c8b98a 60%,#4d7a35)"></div>
  <div class="listing" role="img" aria-label="Brick house" style="background:linear-gradient(180deg,#9fb8d8,#b0705a)">
    <div class="listing-hover"><h3>Beatiful HOUSE</h3><p>Something more beautiful house photos.</p><div class="tools"><span></span><span></span></div></div>
  </div>
  <div class="listing" role="img" aria-label="Modern timber house on a lawn" style="background:linear-gradient(180deg,#4f8ad0,#6d5a44 50%,#5c9a3a)"></div>
  <div class="listing" role="img" aria-label="White villa with pool at night" style="background:linear-gradient(180deg,#1c3f8a,#d8d1b6 60%,#2a5fa8)"></div>
  <div class="listing" role="img" aria-label="Grey two-storey house with deck" style="background:linear-gradient(180deg,#c8ccd2,#7b7b7b 60%,#6a6552)"></div>
  <div class="listing" role="img" aria-label="Log cabin with porch among trees" style="background:linear-gradient(180deg,#4a6a3a,#a8633a 55%,#6a4a2a)"></div>
  <div class="listing" role="img" aria-label="Stone cottage with green lawn" style="background:linear-gradient(180deg,#e6ecf0,#9a9484 50%,#5aa03a)"></div>
  <div class="listing" role="img" aria-label="White mansion with flower garden" style="background:linear-gradient(180deg,#e4ebf2,#d8d0c0 55%,#7a8a4a)"></div>
</div>

<h2 class="abs section-title testi-title">TESTIMONIALS</h2>
<div class="abs testimonial" style="left:123px"><div class="avatar" role="img" aria-label="Customer portrait"></div><time>January 11, 2014</time><p>Lorem ipsum dolor sit amet, consectetur adipiscing. Aliquam viverra &nbsp;dolor sit consectetur.</p></div>
<div class="abs testimonial" style="left:307px"><div class="avatar" role="img" aria-label="Customer portrait"></div><time>January 10, 2014</time><p>Lorem ipsum dolor sit amet, consectetur adipiscing.</p></div>
<div class="abs testimonial" style="left:492px"><div class="avatar" role="img" aria-label="Customer portrait"></div><time>January 09, 2014</time><p>Lorem ipsum dolor sit amet, consectetur adipiscing. Aliquam viverra &nbsp;dolor sit.</p></div>

<footer>
  <div class="abs site-footer"></div>
  <h4 class="abs footer-heading" style="left:125px">CONTACT INFO</h4>
  <h4 class="abs footer-heading" style="left:311px">LATEST NEWS</h4>
  <h4 class="abs footer-heading" style="left:524px">SUBSCRIBE TO OUR NEWSLETTER</h4>
  <div class="abs contact-info">
    <p>58 E. Tamsin Avenue, Ste 410, Corvale Bay, ST 32599 incididunt ut labore et dolore magna aliqua.</p>
    <p>Ph: (555) 261-0948 , Mo: (555) 718-3062</p>
    <p>Email: mirelharrowgate@quellmail.example</p>
  </div>
  <div class="abs social" style="left:125px"></div>
  <div class="abs social" style="left:149px"></div>
  <div class="abs social" style="left:174px"></div>

  <div class="abs news-thumb" style="top:1034px" role="img" aria-label="News photo"></div>
  <div class="abs news-text" style="top:1032px">Vantrel recieve award<br><small>july 7, 2014</small></div>
  <div class="abs news-thumb" style="top:1087px" role="img" aria-label="News photo"></div>
  <div class="abs news-text" style="top:1085px">Vantrel recieve award<br><small>july 7, 2014</small></div>

  <div class="abs newsletter-input">Enter Your Mail Id</div>
  <div class="abs btn-subscribe">Subscribe</div>
  <div class="abs badge" style="left:482px;width:104px"></div>
  <div class="abs badge" style="left:595px;width:70px"></div>

  <div class="abs footer-bar">
    <nav><span style="left:258px">Home</span><span style="left:301px">Features</span><span style="left:353px">onlie aution</span><span style="left:412px">Blog</span><span style="left:452px">Work</span><span style="left:493px">Contact</span></nav>
    <p class="copyright">Copy Right © 2014 All Rights Reserved.</p>
  </div>
  <svg class="abs to-top" viewBox="0 0 17 17"><path d="M5 10 8.5 6.5 12 10" stroke="#fff" fill="none" stroke-width="1.3"/></svg>
</footer>

</body>
</html>
```